AI Business Tools Landing Page

My web-based website builder (Pavlora.com) will be adding many new features in the very near future and I need an eye-catching landing page to promote these new products.

The page will have a primary section of the 8 main products we are promoting:
1. AI Instant Website Generator
2. AI Chatbot
3. Online Store Builder with AI Assistance
4. AI Auto-Blogging System
5. Online Scheduling System
6. Custom Email System
7. SEO Service
8. CRM System

The page will also have a smaller section for links to our affiliate programs. These can be smaller, less-promanent buttons or links. These are the affiliate products:
1. Get Your LLC
2. Website Design and Maintenance
3. Searchly Ads Management
4. Social Media Posting Service
5. Logo Design
6. Trademark Registration
7. Patent Application
8. Printing Services (including postcards, flyers, and merch.)
9. Bulk AI Content Generator

The theme and color scheme of the page should follow the theme of our main website, which is https://pavlora.com.

I need the page fully coded and ready to deploy on my server.

I look forward to seeing your amazing designs!

```html
<!DOCTYPE html>
<html lang="en">
<head>
<meta charset="utf-8">
<title>Pavlora – Artificial Intelligence Business Tools</title>
<link rel="stylesheet" href="https://fonts.googleapis.com/css2?family=Noto+Sans:wght@300;400;600;700&display=swap">
<style>
  :root {
    --navy-bar: #1f3a55;
    --navy-hero: #0a1730;
    --title-blue: #0f3a63;
    --accent: #1a86d9;
    --accent-cyan: #27b8e8;
    --text: #2b2f36;
    --card-border: #e3e7ee;
    --light-band: #e5eef9;
    --white: #ffffff;
  }
  * { box-sizing: border-box; margin: 0; padding: 0; }
  html, body { width: 1200px; height: 2471px; overflow: hidden; background: var(--white); }
  body { font-family: "Noto Sans", sans-serif; color: var(--text); position: relative; }

  .site-header {
    position: absolute; top: 0; left: 0; width: 1200px; height: 86px;
    background: var(--navy-bar);
  }
  .brand { display: flex; align-items: center; gap: 12px; color: var(--white);
    font-family: "Noto Sans", sans-serif; font-weight: 600; }
  .brand-dot { width: 34px; height: 34px; border-radius: 50%; background: var(--accent-cyan); }
  .site-header .brand { position: absolute; left: 50%; top: 50%; transform: translate(-50%, -50%); font-size: 36px; }
  .menu-toggle { position: absolute; left: 1060px; top: 32px; width: 27px; height: 22px; }
  .menu-toggle span { display: block; height: 3px; background: var(--accent-cyan); margin-bottom: 6px; border-radius: 2px; }

  .hero {
    position: absolute; top: 86px; left: 0; width: 1200px; height: 429px;
    background: var(--navy-hero); overflow: hidden;
  }
  .hero-photo {
    position: absolute; inset: 0;
    background:
      radial-gradient(circle at 74% 40%, rgba(255,190,170,0.85) 0 2%, rgba(230,120,110,0.45) 6%, rgba(40,110,170,0.3) 18%, transparent 34%),
      radial-gradient(ellipse at 90% 70%, rgba(120,150,180,0.55), transparent 40%),
      linear-gradient(90deg, #07142a 0%, #0b2140 40%, #123a5e 70%, #1d4f78 100%);
  }
  .hero-curve {
    position: absolute; left: 0; top: 0; width: 520px; height: 429px;
    background: linear-gradient(90deg, var(--navy-hero) 70%, rgba(10,23,48,0));
  }
  .hero-corner {
    position: absolute; left: 0; bottom: 0; width: 150px; height: 150px;
    background: var(--white);
  }
  .hero-corner::after {
    content: ""; position: absolute; inset: 0; background: var(--navy-hero);
    border-bottom-left-radius: 150px;
  }
  .hero-copy { position: absolute; left: 111px; top: 0; color: var(--white); }
  .eyebrow { position: absolute; top: 82px; left: 0; font-size: 19px; font-weight: 400; white-space: nowrap; }
  .hero-title { position: absolute; top: 116px; left: 0; font-size: 57px; line-height: 59px; font-weight: 700; white-space: nowrap; letter-spacing: -0.5px; }
  .hero-rule { position: absolute; top: 262px; left: 0; width: 142px; height: 5px; border-radius: 3px;
    background: linear-gradient(90deg, var(--accent-cyan), var(--accent)); }
  .hero-arrow { position: absolute; top: 352px; left: 0; }

  .products {
    position: absolute; top: 592px; left: 111px; width: 978px;
    display: grid; grid-template-columns: 479px 479px; column-gap: 20px;
    grid-template-rows: 268px 269px 267px 345px; row-gap: 23px;
  }
  .product-card {
    border: 1px solid var(--card-border); border-radius: 10px; background: var(--white);
    box-shadow: 0 2px 8px rgba(15,58,99,0.06); padding: 29px 12px 0 30px; overflow: hidden;
  }
  .product-title { font-size: 24.5px; line-height: 28px; font-weight: 600; color: var(--title-blue); white-space: nowrap; letter-spacing: -0.3px; }
  .title-rule { width: 45px; height: 4px; border-radius: 2px; background: var(--accent-cyan); margin: 12px 0 24px; }
  .feature-list { list-style: none; }
  .feature-list li, .resource-list li {
    position: relative; padding-left: 23px; font-size: 15px; line-height: 28.2px; font-weight: 300; color: var(--text); letter-spacing: -0.15px;
  }
  .feature-list li::before, .resource-list li::before {
    content: ""; position: absolute; left: 0; top: 8px; width: 13px; height: 13px; border-radius: 50%; background: var(--accent);
  }
  .feature-list li::after, .resource-list li::after {
    content: ""; position: absolute; left: 5px; top: 11px; border-left: 5px solid var(--white);
    border-top: 3.5px solid transparent; border-bottom: 3.5px solid transparent;
  }
  .inline-link { color: var(--accent); }

  .resources {
    position: absolute; top: 1862px; left: 0; width: 1200px; height: 463px; background: var(--light-band);
  }
  .resources-title {
    position: absolute; top: 45px; left: 0; width: 1200px; text-align: center;
    font-size: 43px; line-height: 50px; font-weight: 600; color: #1d2330; letter-spacing: -0.3px;
  }
  .resource-list { list-style: none; position: absolute; top: 225px; }
  .resource-list li { font-size: 16px; line-height: 34.4px; padding-left: 27px; white-space: nowrap; letter-spacing: -0.2px; }
  .resource-list li::before { top: 11px; }
  .resource-list li::after { top: 14px; }
  .resource-list.col-one { left: 111px; }
  .resource-list.col-two { left: 419px; }
  .resource-photo {
    position: absolute; left: 757px; top: 189px; width: 332px; height: 215px;
    border-top-left-radius: 60px;
    background:
      radial-gradient(circle at 38% 42%, rgba(255,150,80,0.7) 0 5%, rgba(230,90,50,0.35) 14%, transparent 30%),
      radial-gradient(circle at 70% 75%, rgba(60,170,240,0.6), transparent 25%),
      linear-gradient(135deg, #0c2a4d 0%, #16467a 55%, #2a6aa6 100%);
  }

  .site-footer {
    position: absolute; top: 2325px; left: 0; width: 1200px; height: 146px; background: var(--navy-bar);
  }
  .site-footer .brand { position: absolute; left: 115px; top: 53px; font-size: 31px; }
  .site-footer .brand-dot { width: 32px; height: 32px; }
  .social-links {
    position: absolute; left: 498px; top: 41px; width: 212px;
    display: grid; grid-template-columns: repeat(5, 26px); column-gap: 18px; row-gap: 15px;
  }
  .social-links span { width: 26px; height: 26px; border-radius: 50%; background: var(--white); }
  .copyright { position: absolute; right: 114px; top: 62px; color: var(--white); font-size: 14px; font-weight: 400; }
</style>
</head>
<body>

<header class="site-header">
  <div class="brand"><span class="brand-dot"></span>Pavlora</div>
  <div class="menu-toggle" aria-label="Menu"><span></span><span></span><span></span></div>
</header>

<section class="hero">
  <div class="hero-photo" role="img" aria-label="Human hand reaching toward a robotic hand against a glowing blue digital data background"></div>
  <div class="hero-curve"></div>
  <div class="hero-corner"></div>
  <div class="hero-copy">
    <p class="eyebrow">WELCOME TO PAVLORA</p>
    <h1 class="hero-title">Artificial intelligence<br>Business Tools</h1>
    <div class="hero-rule"></div>
    <svg class="hero-arrow" width="16" height="28" viewBox="0 0 16 28" aria-hidden="true">
      <path d="M8 1 V26 M2 20 L8 26 L14 20" stroke="#ffffff" stroke-width="2" fill="none"/>
    </svg>
  </div>
</section>

<main class="products">
  <article class="product-card">
    <h2 class="product-title">AI Instant Website Generator</h2>
    <div class="title-rule"></div>
    <ul class="feature-list">
      <li>Get a professional, SEO-optimized website in seconds!</li>
      <li>Includes custom domain, secure high-speed hosting, professional images, and more!</li>
    </ul>
  </article>
  <article class="product-card">
    <h2 class="product-title">AI ChatBot</h2>
    <div class="title-rule"></div>
    <ul class="feature-list">
      <li>Fully-trainable ChatBot will learn about your business to automate the customer support process!</li>
      <li>Built-in CRM features integrate emailing, text messaging, and contact forms!</li>
    </ul>
  </article>
  <article class="product-card">
    <h2 class="product-title">Online Store Builder (E-Commerce)<br>with AI Assistance</h2>
    <div class="title-rule"></div>
    <ul class="feature-list">
      <li>Sell you products online and integrate your products into any website!</li>
      <li>Accept payments from multiple payment gateways including Paydeck and Coinway!</li>
    </ul>
  </article>
  <article class="product-card">
    <h2 class="product-title">AI Auto-Blogging System</h2>
    <div class="title-rule"></div>
    <ul class="feature-list">
      <li>AI will generate an incredible blog for your business in seconds and immediately begin posting content for you!</li>
      <li>Choose from daily, weekly, or monthly automated blog posting. Consistent, unique, SEO-optimized content posting on cruise control!</li>
    </ul>
  </article>
  <article class="product-card">
    <h2 class="product-title">Online Scheduling System</h2>
    <div class="title-rule"></div>
    <ul class="feature-list">
      <li>Get appointment bookings, restaurant reservations, or consultations scheduled directly from your website!</li>
      <li>Manage your employees’ schedules and all your appointments from a simple, user-friendly dashboard!</li>
    </ul>
  </article>
  <article class="product-card">
    <h2 class="product-title">Custom emails using your domain</h2>
    <div class="title-rule"></div>
    <ul class="feature-list">
      <li>Quickly set up emails for yourself and all your employees with your own domain extension (example –<span class="inline-link">sam@yourbusiness.com</span>). No more unprofessional Mailbox and Webpost email addresses!</li>
      <li>Manage all your business emails from a simple, user-friendly interface!</li>
    </ul>
  </article>
  <article class="product-card">
    <h2 class="product-title">SEO Service – Automatic Backlink<br>Building</h2>
    <div class="title-rule"></div>
    <ul class="feature-list">
      <li>Let us do the hard work of getting high-quality backlinks to your website. Although difficult to get, backlinks to your website boost search engine ranking more than any other strategy!</li>
      <li>Subscribe now and start getting 10-20 high-quality permanent backlinks to your website every month, guaranteed!</li>
    </ul>
  </article>
  <article class="product-card">
    <h2 class="product-title">Customer Relationship<br>Management (CRM) System</h2>
    <div class="title-rule"></div>
    <ul class="feature-list">
      <li>Automate the lead follow up process to consistently stay in front of your potential customers!</li>
      <li>Schedule automatic email and text campaigns and effortlessly follow your funnels from lead to closing!</li>
    </ul>
  </article>
</main>

<section class="resources">
  <h2 class="resources-title">Additional Resources to Help Launch<br>Your Business</h2>
  <ul class="resource-list col-one">
    <li>Get Your LLC</li>
    <li>Website Design and Maintenance</li>
    <li>Searchly Ads Management</li>
    <li>Social Media Posting Service</li>
    <li>Logo Design</li>
  </ul>
  <ul class="resource-list col-two">
    <li>Trademark Registration</li>
    <li>Patent Application</li>
    <li>Printing Services (including postcards,<br>flyers, and merch.)</li>
    <li>Bulk AI Content Generator</li>
  </ul>
  <div class="resource-photo" role="img" aria-label="Businessman holding a tablet with a glowing AI network graphic above it"></div>
</section>

<footer class="site-footer">
  <div class="brand"><span class="brand-dot"></span>Pavlora</div>
  <nav class="social-links" aria-label="Social networks">
    <span></span><span></span><span></span><span></span><span></span>
    <span></span><span></span><span></span><span></span><span></span>
  </nav>
  <p class="copyright">2024 Pavlora. All Rights Reserved.</p>
</footer>

</body>
</html>
```